Dental office stationary (letterhead, envelopes), business cards, presentation folders

Nothing too dental outside of the logo. I will need all stationary, presentation folders, business cards. Would prefer to stay in the colors of the logo

Gordon Patel, DDS
Bright Haven Dental Implant Center
555-318-2790
info@brighthavendental.example
4817 NW Maple Crest Rd Unit B
Stuart, FL 00000

Also need appointment date and time
And cancellation policy
I want it to say “kindly ask for
A 48hr cancellation policy to avoid incurring a cancellation fee”

Industry/Entity Type

Dental

Colors
0054AA
0677BA
7BADD7
CADEEF
E8F1F8

Requirements
Must have
• Name of your office, name of doctor, address, phone number
Should not have
• Too much tooth/dental. Only the tooth in logo

```html
<!DOCTYPE html>
<html lang="en">
<head>
<meta charset="utf-8">
<title>Bright Haven Dental Implant Center — Envelope</title>
<link href="https://fonts.googleapis.com/css2?family=Montserrat:wght@400;500&display=swap" rel="stylesheet">
<style>
  :root {
    --page-bg: #e9ecef;
    --paper: #ffffff;
    --brand-blue: #327dc0;
    --brand-teal: #1bae97;
    --brand-sky: #2aa7df;
    --ink: #1d1d1f;
  }
  html, body {
    margin: 0;
    padding: 0;
    width: 1200px;
    height: 1200px;
    overflow: hidden;
    background: var(--page-bg);
    font-family: "Montserrat", Arial, sans-serif;
  }
  .canvas {
    position: relative;
    width: 1200px;
    height: 1200px;
  }
  .envelope {
    position: absolute;
    width: 480px;
    height: 740px;
    box-shadow: 0 8px 24px rgba(0,0,0,0.18);
  }
  .envelope-front {
    left: 90px;
    top: 200px;
    background: var(--paper);
    overflow: hidden;
    z-index: 2;
  }
  .envelope-back {
    left: 630px;
    top: 260px;
    background: var(--brand-blue);
    z-index: 1;
  }
  .flap {
    position: absolute;
    left: 0;
    top: 0;
    width: 480px;
    height: 120px;
  }
  .brand-name {
    position: absolute;
    left: 0;
    right: 0;
    text-align: center;
    font-weight: 500;
    font-size: 30px;
    line-height: 1.25;
    letter-spacing: 1px;
    margin: 0;
  }
  .envelope-front .brand-name {
    top: 190px;
    color: var(--brand-teal);
  }
  .envelope-back .brand-name {
    top: 300px;
    color: var(--paper);
  }
  .contact-block {
    position: absolute;
    left: 40px;
    right: 30px;
    bottom: 92px;
    font-size: 14px;
    color: var(--ink);
    line-height: 1.6;
  }
  .contact-office {
    color: var(--brand-sky);
    font-size: 15px;
    margin: 0 0 4px 0;
  }
  .contact-line {
    display: flex;
    align-items: center;
    gap: 8px;
    margin: 0;
    white-space: nowrap;
  }
  .contact-line svg { flex: none; }
  .contact-row { display: flex; gap: 22px; }
  .stripe-teal {
    position: absolute;
    left: 0; right: 0;
    bottom: 58px;
    height: 8px;
    background: var(--brand-teal);
  }
  .stripe-blue {
    position: absolute;
    left: 0; right: 0;
    bottom: 0;
    height: 46px;
    background: var(--brand-blue);
  }
</style>
</head>
<body>
<main class="canvas">
  <section class="envelope envelope-front" aria-label="Envelope front">
    <svg class="flap" viewBox="0 0 480 120" aria-hidden="true">
      <path d="M0 0 H480 V70 Q480 100 450 104 L40 104 Q10 100 0 70 Z" fill="var(--brand-blue)"/>
    </svg>
    <p class="brand-name">Bright Haven<br>Dental Implant Center</p>

    <div class="contact-block">
      <p class="contact-office">Bright Haven Dental Implant Center</p>
      <div class="contact-row">
        <p class="contact-line">
          <svg width="12" height="12" viewBox="0 0 24 24"><path d="M6.6 10.8a15 15 0 0 0 6.6 6.6l2.2-2.2a1 1 0 0 1 1-.25 11.4 11.4 0 0 0 3.6.57 1 1 0 0 1 1 1V20a1 1 0 0 1-1 1A17 17 0 0 1 3 4a1 1 0 0 1 1-1h3.5a1 1 0 0 1 1 1c0 1.25.2 2.45.57 3.57a1 1 0 0 1-.25 1z" fill="var(--brand-sky)"/></svg>
          555-318-2790
        </p>
        <p class="contact-line">
          <svg width="13" height="11" viewBox="0 0 24 20"><rect x="1" y="1" width="22" height="18" rx="2" fill="var(--brand-sky)"/><path d="M2 3l10 8 10-8" stroke="#fff" stroke-width="2" fill="none"/></svg>
          info@brighthavendental.example
        </p>
      </div>
      <p class="contact-line">
        <svg width="11" height="14" viewBox="0 0 20 26"><path d="M10 1a8 8 0 0 0-8 8c0 6 8 16 8 16s8-10 8-16a8 8 0 0 0-8-8z" fill="none" stroke="var(--brand-sky)" stroke-width="3"/></svg>
        4817 NW Maple Crest Rd Unit B, Cedar Bay, ST 00000
      </p>
    </div>

    <div class="stripe-teal"></div>
    <div class="stripe-blue"></div>
  </section>

  <section class="envelope envelope-back" aria-label="Envelope back">
    <p class="brand-name">Bright Haven<br>Dental Implant Center</p>
  </section>
</main>
</body>
</html>
```